Stationery Design Project for Nimbora, Chicago

Nimbora, a street parking application which helps car drivers find a street parking spot by offering an ideal path along which to look for parking. This path is calculated by our algorithm based on data (e.g. historical data, baseball games schedule, etc.). Along this path the driver will find a spot and will also save 70% of the search time. Customer we target is reg. between 21 and 45 yo.

We envision something young, fresh, bright and original. Slightly abstract maybe. It should represent the idea and elements of finding street parking in the city, e.g. car(s), parking spot, people, city, etc. (just ideas!).

Logo is attached.

Requirement:
- Business Cards (2 Sided Full Color CMYK)
- Letterhead (1 Sided Full Color CMYK)
- Envelope (1 Sided Full Color CMYK)
- Sticker (1 Sided Full Color CMYK), round with a 2inch diameter.

Reason: We're starting to get more and more designs and need more time to look into all of them. Very exciting!! Thanks to everybody!

Hi all, we're in the process of selecting our favs. Though choices!!! Really good submissions. Will keep you posted and sorry for the delay.

Target Market(s)

Car drivers and owners between 21 and 45

Industry/Entity Type

Parking

Requirements
Must have
• Sticker should be round and include company URL nimbora.com and the new logo which we will attach soon.
Should not have
• Should not be too serious or boring.

```html
<!DOCTYPE html>
<html lang="en">
<head>
<meta charset="utf-8">
<title>Nimbora Business Cards</title>
<link rel="stylesheet" href="https://fonts.googleapis.com/css2?family=Courier+Prime:wght@400;700&display=swap">
<style>
  :root {
    --backdrop: #e8e5e1;
    --card-white: #ffffff;
    --card-black: #000000;
    --brand-blue: #2a78c4;
    --brand-green: #3fbf4e;
    --ink: #1c1c1c;
    --mono: "Courier Prime", "Courier New", monospace;
  }
  * { box-sizing: border-box; margin: 0; padding: 0; }
  html, body {
    width: 1124px; height: 1200px; overflow: hidden;
    background: var(--backdrop);
    font-family: var(--mono);
  }
  .canvas { position: relative; width: 1124px; height: 1200px; }
  .card {
    position: absolute; left: 144px; width: 846px; height: 481px;
    border-radius: 36px; overflow: hidden;
  }
  .card-front { top: 92px; background: var(--card-white); box-shadow: 0 6px 18px rgba(0,0,0,.18); }
  .card-back { top: 619px; background: var(--card-black); box-shadow: 0 6px 18px rgba(0,0,0,.25); }

  .brand { position: absolute; left: 47px; top: 190px; display: flex; align-items: center; gap: 14px; }
  .brand-dot { width: 112px; height: 112px; border-radius: 50%; background: var(--brand-blue); }
  .brand-name { font-weight: 700; font-size: 58px; color: var(--ink); letter-spacing: -1px; }

  .url-strip {
    position: absolute; left: 450px; top: 102px; width: 33px; height: 287px;
    background: var(--brand-blue);
  }
  .url-strip span {
    position: absolute; left: 50%; top: 50%;
    transform: translate(-50%, -50%) rotate(-90deg);
    color: #fff; font-weight: 700; font-size: 20px; white-space: nowrap; letter-spacing: 1px;
  }
  .contact-panel {
    position: absolute; left: 489px; top: 102px; width: 357px; height: 287px;
    background: var(--card-black); color: var(--brand-green);
    padding: 10px 0 0 29px;
  }
  .contact-panel .name { font-weight: 700; font-size: 27px; line-height: 34px; }
  .contact-panel .title { font-size: 22px; line-height: 30px; margin-bottom: 14px; }
  .contact-panel .line { font-size: 22px; line-height: 31px; display: flex; align-items: center; gap: 6px; }
  .contact-panel .line svg { width: 15px; height: 15px; fill: var(--brand-green); flex: none; }
  .contact-panel .address { font-size: 22px; line-height: 32px; margin-top: 16px; }

  .back-mark {
    position: absolute; left: 50%; top: 54px; transform: translateX(-50%);
    width: 260px; height: 260px; border-radius: 50%; background: var(--brand-blue);
    display: flex; align-items: center; justify-content: center;
  }
  .back-mark span { color: #fff; font-weight: 700; font-size: 44px; }
  .back-url {
    position: absolute; left: 0; right: 0; top: 372px; text-align: center;
    color: var(--brand-green); font-weight: 700; font-size: 38px; letter-spacing: 2px;
  }
</style>
</head>
<body>
<main class="canvas">
  <section class="card card-front">
    <div class="brand">
      <div class="brand-dot"></div>
      <div class="brand-name">nimbora</div>
    </div>
    <div class="url-strip"><span>www.nimbora.com</span></div>
    <div class="contact-panel">
      <p class="name">Your Name</p>
      <p class="title">Title</p>
      <p class="line"><svg viewBox="0 0 16 16"><path d="M3 1l3 3-2 2c1 2 3 4 5 5l2-2 3 3-2 3C7 15 1 9 1 3z"/></svg>123-456-789</p>
      <p class="line"><svg viewBox="0 0 16 16"><path d="M4 0h8v16H4zM5.5 2v10h5V2z"/></svg>123-456-789</p>
      <p class="line"><svg viewBox="0 0 16 16"><path d="M1 3h14v2L8 9 1 5zM1 7l7 4 7-4v6H1z"/></svg>info@nimbora-mail.com</p>
      <p class="address">Complex name, Street<br>State, zip code</p>
    </div>
  </section>
  <section class="card card-back">
    <div class="back-mark"><span>nimbora</span></div>
    <p class="back-url">www.nimbora.com</p>
  </section>
</main>
</body>
</html>
```